TALMORK

The business want a professional looking business card. We have a scetch we will add but want the extra upgrade, and would like more suggestions for variations of our business cards.

```html
<!DOCTYPE html>
<html lang="en">
<head>
<meta charset="UTF-8">
<title>TALMORK Business Card</title>
<link rel="stylesheet" href="https://fonts.googleapis.com/css2?family=Cinzel:wght@500;700&family=Montserrat:wght@400;500&display=swap">
<style>
  :root {
    --navy: #040c1b;
    --navy-soft: #0d1a30;
    --gold: #b8862b;
    --gold-light: #d9b25a;
    --cream: #f6e8de;
    --brown: #5a3a10;
    --ink: #3a2a1a;
    --page: #ffffff;
  }
  * { margin: 0; padding: 0; box-sizing: border-box; }
  html, body { width: 1200px; height: 2457px; overflow: hidden; background: var(--page); }
  .canvas { position: relative; width: 1200px; height: 2457px; }

  .card {
    position: absolute;
    left: 181px;
    width: 838px;
    height: 479px;
    border: 3px solid var(--gold);
    box-shadow: 0 24px 40px rgba(0,0,0,0.18);
    overflow: hidden;
  }
  .card-front { top: 684px; background: var(--navy); }
  .card-back { top: 1293px; background: var(--cream); }

  .pattern-area {
    position: absolute;
    top: 0;
    height: 100%;
    background: radial-gradient(ellipse at center, var(--navy-soft) 0%, var(--navy) 70%);
  }
  .pattern-left { left: 0; width: 175px; }
  .pattern-right { right: 0; width: 175px; }

  .brand-dot {
    position: absolute;
    left: 50%;
    top: 120px;
    width: 90px;
    height: 90px;
    margin-left: -45px;
    border-radius: 50%;
    background: var(--gold);
  }
  .brand-name {
    font-family: "Cinzel", serif;
    font-weight: 500;
    color: var(--gold);
    letter-spacing: 0.22em;
    white-space: nowrap;
  }
  .tagline {
    font-family: "Montserrat", sans-serif;
    font-weight: 500;
    color: var(--gold);
    letter-spacing: 0.4em;
    white-space: nowrap;
  }
  .card-front .brand-name {
    position: absolute; left: 0; right: 0; top: 258px;
    text-align: center; font-size: 42px; padding-left: 0.22em;
  }
  .card-front .tagline {
    position: absolute; left: 0; right: 0; top: 315px;
    text-align: center; font-size: 13px; padding-left: 0.4em;
  }
  .front-web {
    position: absolute; left: 126px; right: 126px; top: 352px;
    display: flex; align-items: center; gap: 16px;
  }
  .front-web .rule { flex: 1; height: 1px; background: var(--gold); opacity: 0.6; }
  .front-web span {
    font-family: "Montserrat", sans-serif;
    font-size: 30px; color: var(--gold-light);
  }

  .side-band {
    position: absolute; left: 0; top: 0; width: 172px; height: 100%;
    background: radial-gradient(ellipse at center, var(--navy-soft) 0%, var(--navy) 70%);
    border-right: 3px solid var(--gold);
  }
  .back-content { position: absolute; left: 219px; top: 0; right: 50px; height: 100%; }
  .back-content .brand-name { position: absolute; top: 55px; font-size: 46px; }
  .back-content .tagline { position: absolute; top: 123px; left: 78px; font-size: 14px; }
  .person-name {
    position: absolute; top: 148px;
    font-family: "Cinzel", serif; font-weight: 700;
    font-size: 41px; color: var(--brown); white-space: nowrap;
  }
  .person-role {
    position: absolute; top: 198px;
    font-family: "Montserrat", sans-serif; font-size: 24px; color: var(--ink);
  }
  .divider { position: absolute; top: 260px; left: 0; width: 546px; height: 1px; background: #8a7560; }
  .contact-list { position: absolute; top: 296px; left: 0; list-style: none; }
  .contact-item {
    display: flex; align-items: center; gap: 14px; height: 44px;
    font-family: "Montserrat", sans-serif; font-size: 27px; color: var(--ink);
  }
  .contact-icon {
    width: 26px; height: 26px; border-radius: 50%; background: var(--navy);
    display: flex; align-items: center; justify-content: center; flex-shrink: 0;
  }
</style>
</head>
<body>
<main class="canvas">
  <section class="card card-front">
    <div class="pattern-area pattern-left" role="img" aria-label="Faint gold line-art leaf and circle ornament"></div>
    <div class="pattern-area pattern-right" role="img" aria-label="Faint gold line-art leaf and circle ornament"></div>
    <div class="brand-dot"></div>
    <div class="brand-name">TALMORK</div>
    <div class="tagline">SINCE 2026</div>
    <div class="front-web"><div class="rule"></div><span>www.talmork.llc</span><div class="rule"></div></div>
  </section>

  <section class="card card-back">
    <div class="side-band" role="img" aria-label="Navy band with faint gold line-art leaf ornament"></div>
    <div class="back-content">
      <div class="brand-name">TALMORK</div>
      <div class="tagline">SINCE 2026</div>
      <div class="person-name">ARNE MIKAEL VESTBYE</div>
      <div class="person-role">CEO &amp; Founder</div>
      <div class="divider"></div>
      <ul class="contact-list">
        <li class="contact-item">
          <span class="contact-icon"><svg width="12" height="16" viewBox="0 0 12 16"><rect x="1.5" y="1" width="9" height="14" rx="1.5" fill="none" stroke="#fff" stroke-width="1.5"/><circle cx="6" cy="12.5" r="0.9" fill="#fff"/></svg></span>
          004790518274
        </li>
        <li class="contact-item">
          <span class="contact-icon"><svg width="14" height="11" viewBox="0 0 14 11"><rect x="1" y="1" width="12" height="9" fill="none" stroke="#fff" stroke-width="1.3"/><path d="M1 1 L7 6 L13 1" fill="none" stroke="#fff" stroke-width="1.3"/></svg></span>
          talmork.llc@mailbox.com
        </li>
        <li class="contact-item">
          <span class="contact-icon"><svg width="14" height="14" viewBox="0 0 14 14"><circle cx="7" cy="7" r="6" fill="none" stroke="#fff" stroke-width="1.2"/><ellipse cx="7" cy="7" rx="2.6" ry="6" fill="none" stroke="#fff" stroke-width="1.2"/><path d="M1 7 H13" stroke="#fff" stroke-width="1.2"/></svg></span>
          www.talmork.llc
        </li>
      </ul>
    </div>
  </section>
</main>
</body>
</html>
```